Redesign of business card for Cedar Ridge Mechanical

We are looking for a new design for our business cards for Cedar Ridge Mechanical. We are a plumbing & HVAC construction company, operating on the West Coast of Canada and USA. Logo attached.
Industry/Entity Type
Construction - Plumbing & HVAC
Contact Information for Business Card
Name, address, phone numbers, email, website address
Look and feel
Each slider illustrates characteristics of the customer's brand and the style your logo design should communicate.

```html
<!DOCTYPE html>
<html lang="en">
<head>
<meta charset="UTF-8">
<title>Cedar Ridge Mechanical – Business Card</title>
<link href="https://fonts.googleapis.com/css2?family=Montserrat:wght@400;700&display=swap" rel="stylesheet">
<style>
  :root {
    --backdrop: #222222;
    --card: #ffffff;
    --ink: #111111;
    --ink-soft: #2b2b2b;
  }
  * { margin: 0; padding: 0; box-sizing: border-box; }
  html, body {
    width: 1200px;
    height: 780px;
    overflow: hidden;
    background: var(--backdrop);
    font-family: "Montserrat", sans-serif;
  }
  .stage {
    position: relative;
    width: 1200px;
    height: 780px;
    display: flex;
    align-items: center;
    justify-content: center;
    gap: 40px;
  }
  .card {
    position: relative;
    width: 540px;
    height: 309px;
    background: var(--card);
    color: var(--ink);
    overflow: hidden;
  }

  /* Front */
  .card-front {
    display: flex;
    align-items: center;
    justify-content: center;
  }
  .front-wordmark {
    display: flex;
    align-items: center;
    gap: 18px;
  }
  .wordmark-square {
    width: 44px;
    height: 44px;
    background: var(--ink);
    flex-shrink: 0;
  }
  .front-wordmark .company-name {
    font-weight: 700;
    font-size: 26px;
    line-height: 1.15;
    letter-spacing: 1px;
    text-transform: uppercase;
  }

  /* Back */
  .back-wordmark {
    position: absolute;
    top: 30px;
    left: 34px;
    display: flex;
    align-items: center;
    gap: 9px;
  }
  .back-wordmark .wordmark-square {
    width: 18px;
    height: 18px;
  }
  .back-wordmark .company-name {
    font-weight: 700;
    font-size: 12px;
    letter-spacing: 0.6px;
    text-transform: uppercase;
  }
  .contact {
    position: absolute;
    left: 34px;
    top: 96px;
    font-size: 11.5px;
    color: var(--ink-soft);
    line-height: 1.55;
  }
  .contact .address { margin-bottom: 6px; }
  .contact-list { list-style: none; }
  .contact-list li {
    display: flex;
    align-items: center;
    gap: 8px;
  }
  .contact-list svg {
    width: 10px;
    height: 10px;
    fill: var(--ink);
    flex-shrink: 0;
  }
  .person {
    position: absolute;
    right: 46px;
    bottom: 58px;
    text-align: right;
  }
  .person-name {
    font-weight: 700;
    font-size: 17px;
    letter-spacing: 0.5px;
    text-transform: uppercase;
  }
  .person-title {
    font-size: 12px;
    color: var(--ink-soft);
    margin-top: 2px;
  }
  .edge-tab {
    position: absolute;
    right: 0;
    bottom: 52px;
    width: 22px;
    height: 40px;
    background: var(--ink);
  }
</style>
</head>
<body>
<main class="stage">
  <section class="card card-front" aria-label="Card front">
    <div class="front-wordmark">
      <span class="wordmark-square"></span>
      <span class="company-name">Cedar Ridge<br>Mechanical</span>
    </div>
  </section>

  <section class="card card-back" aria-label="Card back">
    <div class="back-wordmark">
      <span class="wordmark-square"></span>
      <span class="company-name">Cedar Ridge Mechanical</span>
    </div>

    <div class="contact">
      <p class="address">2150 Harbour Road,<br>Vancouver BC V5K 1A1</p>
      <ul class="contact-list">
        <li>
          <svg viewBox="0 0 10 10" aria-hidden="true"><path d="M1 1.5 3 1l1 2.2-1.1.8a5 5 0 0 0 3.1 3.1l.8-1.1L9 7l-.5 2C4.5 9 1 5.5 1 1.5z"/></svg>
          604 555 0182
        </li>
        <li>
          <svg viewBox="0 0 10 10" aria-hidden="true"><path d="M0.5 2h9v6h-9z M1.2 2.6 5 5.4l3.8-2.8" stroke="#fff" stroke-width="0.8"/></svg>
          info@cedarridgemech.com
        </li>
        <li>
          <svg viewBox="0 0 10 10" aria-hidden="true"><circle cx="5" cy="5" r="4.5"/><path d="M0.5 5h9M5 0.5c-2 2.5-2 6.5 0 9M5 0.5c2 2.5 2 6.5 0 9" stroke="#fff" stroke-width="0.6" fill="none"/></svg>
          www.cedarridgemech.com
        </li>
      </ul>
    </div>

    <div class="person">
      <p class="person-name">Daniel Hale</p>
      <p class="person-title">Managing Director</p>
    </div>
    <span class="edge-tab"></span>
  </section>
</main>
</body>
</html>
```